Clinic for cellulit and fat removal

Name of clinic :
Lirava
- Body & Health (this has to be written on the site.)
I need CMS for me to be able to make changes myself.
A webpage for woman searching for a solution to remove fat and cellulit.
The owner is a brazilian woman in Denmark, and want her sense of aestetic shines thru the website.
There needs to be a slide show on the landing page showing big sliding pictures, of the clinic and and the treatments.
The Cryolipolysis, is a treatment freezing fat and cellulit, and this treatment will be the Attraction of the clinic.
Needs These pages in a horisontal fasion. (written in Danish)
Lirava
Behandlinger
- Cryolipolysis
- Trimflox
- Lymfemassage
- Korathelix
- Amberline Tide
Produkter
Priser
Kontakt
Clinic
Coded - Design and coding required
5+ page

```html
<!DOCTYPE html>
<html lang="en">
<head>
<meta charset="utf-8">
<title>Lirava – Body &amp; Health</title>
<link href="https://fonts.googleapis.com/css2?family=Josefin+Sans:wght@300;400;600;700&family=Open+Sans:wght@400;600;700&display=swap" rel="stylesheet">
<style>
:root{
  --teal:#5bbfcc;
  --teal-mid:#6bc9d3;
  --teal-light:#7bd5de;
  --teal-text:#55b8c5;
  --ink:#3d3d3d;
  --muted:#666;
  --soft:#ebebeb;
  --panel:#e6e6e6;
  --line:#dcdcdc;
  --white:#fff;
}
*{margin:0;padding:0;box-sizing:border-box}
html,body{width:1200px;height:4554px;overflow:hidden}
body{position:relative;background:var(--white);font-family:"Open Sans",sans-serif;color:var(--ink)}
.abs{position:absolute}
.head-font{font-family:"Josefin Sans",sans-serif}
.btn{position:absolute;display:flex;align-items:center;justify-content:center;background:var(--teal);color:var(--white);font-family:"Josefin Sans",sans-serif;font-weight:700;font-size:14px;letter-spacing:.5px;text-transform:uppercase;padding-top:3px}
.btn.outline{background:var(--white);color:var(--teal)}
.photo{position:absolute}
.section-title{position:absolute;left:0;width:1200px;text-align:center;font-family:"Josefin Sans",sans-serif;font-weight:700;font-size:29px;color:var(--teal-text);letter-spacing:.5px}

/* header */
.site-header{position:absolute;top:0;left:0;width:1200px;height:120px;background:var(--white)}
.logo{position:absolute;font-family:"Josefin Sans",sans-serif;font-weight:300;color:var(--teal);letter-spacing:1px}
.site-header .logo{left:130px;top:32px;font-size:56px}
.book-top{left:530px;top:23px;width:290px;height:30px;font-size:11px;font-family:"Open Sans",sans-serif;font-weight:600;gap:8px}
.lang{position:absolute;top:23px;height:30px;border:1px solid var(--line);font-size:10px;color:var(--muted);display:flex;align-items:center;justify-content:center;gap:6px}
.flag{width:13px;height:9px;display:inline-block}
.search-btn{position:absolute;left:1039px;top:23px;width:30px;height:30px;background:var(--teal);display:flex;align-items:center;justify-content:center}
.main-nav a{position:absolute;top:78px;font-size:11px;font-weight:600;color:var(--ink);text-decoration:none;letter-spacing:.4px}

/* hero */
.hero{position:absolute;top:120px;left:0;width:1200px;height:610px;background:linear-gradient(120deg,#e7e2de 0%,#cdb9ab 35%,#efefef 60%,#d9dde2 100%)}
.hero-title{position:absolute;left:740px;top:320px;font-family:"Josefin Sans",sans-serif;font-weight:700;font-size:64px;line-height:70px;color:var(--white)}
.hero .btn{left:746px;top:483px;width:322px;height:60px;font-size:16px;background:#5cc0cd}
.dots{position:absolute;display:flex;gap:17px;align-items:center}
.dot{width:9px;height:9px;border-radius:50%;background:var(--white)}
.dot.on{width:13px;height:13px;background:var(--teal);border:2px solid var(--white)}

/* info band */
.info{position:absolute;top:730px;height:184px;width:400px}
.info h4{position:absolute;left:131px;top:36px;font-family:"Josefin Sans",sans-serif;font-size:16px;font-weight:700;color:var(--white)}
.info p{position:absolute;left:131px;top:64px;font-size:15px;color:var(--white)}
.info .icon{position:absolute;left:42px;top:36px}
.info .btn{left:131px;top:111px;width:135px;height:34px}

/* welcome */
.welcome{position:absolute;left:258px;top:914px;width:684px;height:394px;background:var(--white);box-shadow:0 4px 14px rgba(0,0,0,.12);text-align:center}
.welcome .kicker{margin-top:52px;font-family:"Josefin Sans",sans-serif;font-weight:600;font-size:15px;color:var(--teal-text);letter-spacing:.5px}
.welcome .logo{position:static;font-size:62px;margin-top:8px}
.welcome p{width:540px;margin:20px auto 0;font-size:15px;line-height:30px;color:var(--ink)}
.welcome .btn{left:277px;top:304px;width:130px;height:37px}

/* what is */
.what-panel{position:absolute;left:649px;top:1461px;width:419px;height:423px;background:var(--panel)}
.what-panel h3{position:absolute;left:53px;top:44px;width:340px;font-family:"Josefin Sans",sans-serif;font-weight:400;font-size:26px;line-height:35px;color:var(--teal-text)}
.what-panel p{position:absolute;left:53px;top:166px;width:320px;font-size:12.5px;line-height:26.5px;color:var(--ink);text-align:justify}
.what-panel .btn{left:56px;top:336px;width:131px;height:36px}
.play{position:absolute;left:343px;top:1630px;width:96px;height:62px;background:var(--teal);opacity:.9;display:flex;align-items:center;justify-content:center}

/* before after */
.ba-band{position:absolute;left:0;top:1953px;width:1200px;height:498px;background:var(--soft)}
.ba-title{position:absolute;left:505px;top:62px;font-family:"Josefin Sans",sans-serif;font-weight:700;font-size:29px;color:var(--teal-text)}
.thumb{position:absolute;width:180px;height:103px}

/* testimonials */
.quote-card{position:absolute;top:2624px;width:441px;height:294px;background:var(--white);border:1px solid var(--line)}
.quote-card .mark{position:absolute;left:26px;top:10px;font-family:Georgia,serif;font-size:96px;line-height:96px;color:#d5d5d5}
.quote-card p{position:absolute;left:74px;top:72px;width:335px;font-size:14px;line-height:26.5px;color:var(--ink)}
.quote-card .avatar{position:absolute;left:74px;top:208px;width:58px;height:58px;border-radius:50%;background:radial-gradient(circle at 50% 40%,#bdbdbd,#7a7a7a)}
.quote-card .name{position:absolute;left:150px;top:220px;font-size:11px;font-weight:700;color:var(--ink)}
.quote-card .place{position:absolute;left:150px;top:238px;font-size:10px;color:var(--muted)}
.arrow{position:absolute}

/* cellulit */
.cell-band{position:absolute;left:0;top:3006px;width:1200px;height:537px;background:var(--soft)}
.cell-band h2{position:absolute;left:136px;top:62px;font-family:"Josefin Sans",sans-serif;font-weight:700;font-size:29px;color:var(--teal-text)}
.cell-band .lead{position:absolute;left:136px;top:110px;width:520px;font-size:21px;line-height:35px;color:var(--ink)}
.check-list{position:absolute;left:136px;top:200px;list-style:none;width:460px}
.check-list li{position:relative;padding-left:39px;font-size:14px;line-height:27px;color:var(--ink);margin-bottom:27px}
.check-list li svg{position:absolute;left:2px;top:7px}
.cell-band .btn{left:143px;top:434px;width:131px;height:36px}

/* news */
.news-head{position:absolute;left:0;top:3613px;width:1200px;text-align:center;font-family:"Josefin Sans",sans-serif;font-weight:700;font-size:29px;color:var(--teal-text)}
.news-card{position:absolute;top:3714px;width:283px;height:368px;background:var(--white);border:1px solid var(--line)}
.news-card .photo{left:0;top:0;width:281px;height:156px}
.news-card h5{position:absolute;left:34px;top:174px;width:230px;font-weight:400;font-size:15px;line-height:23px;color:var(--ink)}
.news-card p{position:absolute;left:34px;top:233px;width:220px;font-size:10.5px;line-height:19.5px;color:var(--muted)}
.news-card .btn{left:36px;top:313px;width:98px;height:26px;font-size:11px}

/* footer */
.site-footer{position:absolute;left:0;top:4135px;width:1200px;height:419px;background:var(--soft)}
.site-footer .logo{left:134px;top:126px;font-size:58px}
.foot-h{position:absolute;top:60px;font-size:11px;font-weight:700;color:var(--teal-text);letter-spacing:.4px}
.foot-row{position:absolute;font-size:11px;line-height:21px;color:var(--ink)}
.foot-menu{position:absolute;left:677px;top:97px;font-size:11px;line-height:21px;color:var(--ink)}
.email-box{position:absolute;left:832px;top:106px;width:235px;height:42px;background:var(--white);border:1px solid #cfcfcf;font-size:11px;color:var(--muted);display:flex;align-items:center;padding-left:20px;gap:16px}
.site-footer .signup{left:975px;top:167px;width:92px;height:31px}
.foot-rule{position:absolute;left:132px;top:304px;width:936px;height:1px;background:#cfcfcf}
.follow{position:absolute;left:130px;top:354px;font-size:10px;font-weight:700;color:var(--teal-text)}
.social{position:absolute;top:349px;width:20px;height:20px;background:var(--teal)}
.copy{position:absolute;right:133px;top:354px;font-size:10px;color:var(--ink)}
</style>
</head>
<body>

<header class="site-header">
  <div class="logo">LIRAVA</div>
  <div class="btn book-top">
    <svg width="12" height="12" viewBox="0 0 24 24"><path fill="#fff" d="M6.6 10.8a15.2 15.2 0 0 0 6.6 6.6l2.2-2.2c.3-.3.7-.4 1-.2 1.1.4 2.3.6 3.6.6.6 0 1 .4 1 1V20c0 .6-.4 1-1 1A17 17 0 0 1 3 4c0-.6.4-1 1-1h3.5c.6 0 1 .4 1 1 0 1.3.2 2.5.6 3.6.1.3 0 .7-.2 1z"/></svg>
    BOOK APPOINTMENT (555) 201-4470
  </div>
  <div class="lang" style="left:868px;width:71px"><span class="flag" style="background:#c8102e"></span>Danish</div>
  <div class="lang" style="left:949px;width:78px"><span class="flag" style="background:#2a3f8f"></span>English</div>
  <div class="search-btn"><svg width="14" height="14" viewBox="0 0 24 24"><circle cx="10" cy="10" r="6.5" fill="none" stroke="#fff" stroke-width="3"/><path d="M15 15l6 6" stroke="#fff" stroke-width="3"/></svg></div>
  <nav class="main-nav">
    <a style="left:530px">LIRAVA</a>
    <a style="left:631px">BEHANDLINGER</a>
    <svg class="abs" style="left:735px;top:79px" width="12" height="8" viewBox="0 0 12 8"><path d="M1 1l5 5 5-5" fill="none" stroke="#5bbfcc" stroke-width="2"/></svg>
    <a style="left:800px">PRODUKTER</a>
    <a style="left:926px">PRISER</a>
    <a style="left:1012px">KONTAKT</a>
  </nav>
</header>

<section class="hero">
  <div class="photo" role="img" aria-label="Woman relaxing on a treatment bed while a therapist applies a cryolipolysis device to her abdomen" style="inset:0"></div>
  <h1 class="hero-title">BODY &amp;<br>HEALTH</h1>
  <div class="btn">BOOK A CONSULTATION TODAY</div>
  <div class="dots" style="left:546px;top:545px">
    <span class="dot"></span><span class="dot on"></span><span class="dot"></span><span class="dot"></span><span class="dot"></span>
  </div>
</section>

<section>
  <div class="info" style="left:0;background:var(--teal)">
    <svg class="icon" width="50" height="50" viewBox="0 0 50 50"><circle cx="25" cy="25" r="21" fill="none" stroke="#fff" stroke-width="4"/><path d="M25 13v13h-8" fill="none" stroke="#fff" stroke-width="4"/></svg>
    <h4>OPENING TIMES:</h4>
    <p>Mon - Fri 8 - 8, Sat 9 - 5</p>
    <div class="btn outline">CALL US NOW</div>
  </div>
  <div class="info" style="left:400px;background:var(--teal-mid)">
    <svg class="icon" style="left:38px" width="46" height="48" viewBox="0 0 46 48"><rect x="3" y="8" width="40" height="37" fill="none" stroke="#fff" stroke-width="3"/><rect x="3" y="8" width="40" height="8" fill="#fff"/><path d="M12 3v9M34 3v9" stroke="#fff" stroke-width="3"/><g fill="#fff"><rect x="9" y="21" width="6" height="5"/><rect x="20" y="21" width="6" height="5"/><rect x="31" y="21" width="6" height="5"/><rect x="9" y="31" width="6" height="5"/><rect x="20" y="31" width="6" height="5"/><rect x="31" y="31" width="6" height="5"/></g></svg>
    <h4 style="left:117px">BOOK APPOINTMENTS</h4>
    <p style="left:117px">But I must explain to you how</p>
    <div class="btn outline" style="left:117px">BOOK NOW</div>
  </div>
  <div class="info" style="left:800px;background:var(--teal-light)">
    <svg class="icon" style="left:38px" width="48" height="46" viewBox="0 0 48 46"><rect x="4" y="14" width="40" height="10" fill="#fff"/><rect x="8" y="26" width="32" height="18" fill="#fff"/><rect x="21" y="14" width="6" height="30" fill="#7bd5de"/><path d="M24 14c-4-10-14-10-12-3 1 3 8 3 12 3zm0 0c4-10 14-10 12-3-1 3-8 3-12 3z" fill="none" stroke="#fff" stroke-width="3"/></svg>
    <h4 style="left:110px">SPECIAL OFFERS</h4>
    <p style="left:110px">Find out this months' seasonal offer!</p>
    <div class="btn outline" style="left:110px">FIND OUT NOW</div>
  </div>
</section>

<section class="welcome">
  <div class="kicker">WELCOME TO</div>
  <div class="logo">LIRAVA</div>
  <p>There are many variations of passages of Lorem Ipsum available, but the majority have suffered alteration in some form by injected humour, or randomised words which don't.</p>
  <div class="btn">READ MORE</div>
</section>

<h2 class="section-title" style="top:1376px">WHAT IS LIRAVA?</h2>
<div class="photo" role="img" aria-label="Video still of hands pinching abdominal fat" style="left:132px;top:1461px;width:517px;height:423px;background:linear-gradient(160deg,#5a4a45 0%,#c9a08e 45%,#d8b3a0 60%,#2a2a2a 100%)"></div>
<div class="play"><svg width="26" height="28" viewBox="0 0 26 28"><path d="M2 2l22 12L2 26z" fill="#fff"/></svg></div>
<section class="what-panel">
  <h3>It is a long established fact reader will be distracted by readable content</h3>
  <p>There are many variations of passages of Lorem Ipsum available, but the majority have suffered alteration in some form, by injected humour, or randomised words which don't look even slightly believable.</p>
  <div class="btn">READ MORE</div>
</section>

<section class="ba-band">
  <div class="photo" role="img" aria-label="Slim waist with marker lines drawn on the skin above jeans" style="left:0;top:0;width:504px;height:498px;background:linear-gradient(180deg,#f0f0f0 0%,#e3c9ba 40%,#d8b6a3 70%,#3e5878 85%,#2f4766 100%)"></div>
  <h2 class="ba-title">BEFORE &amp; AFTER PHOTOS</h2>
  <div class="thumb photo" role="img" aria-label="Before and after photo, hips in bikini" style="left:511px;top:132px;background:linear-gradient(90deg,#e6c3ae,#f2b6c8)"></div>
  <div class="thumb photo" role="img" aria-label="Before and after photo, hips" style="left:703px;top:132px;background:linear-gradient(90deg,#f0c9b5,#e9b9a2)"></div>
  <div class="thumb photo" role="img" aria-label="Before and after photo, torso in white shirt" style="left:895px;top:132px;background:linear-gradient(90deg,#f4f4f4,#e2cfc4)"></div>
  <div class="thumb photo" role="img" aria-label="Before and after photo, waist" style="left:511px;top:249px;background:linear-gradient(90deg,#d9a98d,#8fa6c9)"></div>
  <div class="thumb photo" role="img" aria-label="Before and after photo, waist in underwear" style="left:703px;top:249px;background:linear-gradient(90deg,#f1d0bf,#e8c2af)"></div>
  <div class="thumb photo" role="img" aria-label="Before and after photo, waist in jeans" style="left:895px;top:249px;background:linear-gradient(90deg,#3b3b45,#d8b6a3 50%,#5a7aa6)"></div>
  <div class="dots" style="left:514px;top:383px;gap:13px">
    <span class="dot" style="background:#c8c8c8"></span><span class="dot" style="background:#c8c8c8"></span><span class="dot on" style="border-color:var(--soft)"></span><span class="dot" style="background:#c8c8c8"></span><span class="dot" style="background:#c8c8c8"></span><span class="dot" style="background:#c8c8c8"></span>
  </div>
  <div class="btn" style="left:922px;top:385px;width:154px;height:32px;font-size:12px">VIEW MORE PHOTOS</div>
</section>

<h2 class="section-title" style="top:2527px">CLIENT TESTIMONIALS</h2>
<svg class="arrow" style="left:64px;top:2748px" width="22" height="36" viewBox="0 0 22 36"><path d="M19 2L4 18l15 16" fill="none" stroke="#999" stroke-width="3"/></svg>
<svg class="arrow" style="left:1112px;top:2748px" width="22" height="36" viewBox="0 0 22 36"><path d="M3 2l15 16L3 34" fill="none" stroke="#999" stroke-width="3"/></svg>
<article class="quote-card" style="left:132px">
  <div class="mark">&ldquo;</div>
  <p>There are many variations of passages of Lorem Ipsum available, but the majority have suffered alteration in some form, by injected humour, or randomised.</p>
  <div class="avatar" role="img" aria-label="Client portrait"></div>
  <div class="name">TOMAS HERLEV</div>
  <div class="place">England</div>
</article>
<article class="quote-card" style="left:627px">
  <div class="mark">&ldquo;</div>
  <p>There are many variations of passages of Lorem Ipsum available, but the majority have suffered alteration in some form, by injected humour, or randomised.</p>
  <div class="avatar" role="img" aria-label="Client portrait"></div>
  <div class="name">TOMAS HERLEV</div>
  <div class="place">England</div>
</article>

<section class="cell-band">
  <h2>CELLULIT</h2>
  <p class="lead">It is a long established fact reader will be distracted by readable content</p>
  <ul class="check-list">
    <li><svg width="16" height="16" viewBox="0 0 16 16"><circle cx="8" cy="8" r="8" fill="#5bbfcc"/><path d="M4 8l3 3 5-6" fill="none" stroke="#fff" stroke-width="2"/></svg>There are many variations of passages of Lorem Ipsum</li>
    <li><svg width="16" height="16" viewBox="0 0 16 16"><circle cx="8" cy="8" r="8" fill="#5bbfcc"/><path d="M4 8l3 3 5-6" fill="none" stroke="#fff" stroke-width="2"/></svg>At vero eos et accusamus et iusto odio dignissimos ducimus qui blanditiis praesentium</li>
    <li><svg width="16" height="16" viewBox="0 0 16 16"><circle cx="8" cy="8" r="8" fill="#5bbfcc"/><path d="M4 8l3 3 5-6" fill="none" stroke="#fff" stroke-width="2"/></svg>On the other hand, we denounce with righteous indignation and dislike</li>
  </ul>
  <div class="btn">READ MORE</div>
  <div class="photo" role="img" aria-label="Woman in white sitting barefoot, hugging her knees" style="left:520px;top:30px;width:590px;height:480px;background:radial-gradient(ellipse at 62% 50%,#e9cdbd 0%,#e3c4b2 30%,rgba(235,235,235,0) 70%)"></div>
</section>

<svg class="arrow" style="left:452px;top:3616px" width="16" height="30" viewBox="0 0 16 30"><path d="M14 2L3 15l11 13" fill="none" stroke="#999" stroke-width="3"/></svg>
<h2 class="news-head">LATEST NEWS</h2>
<svg class="arrow" style="left:716px;top:3616px" width="16" height="30" viewBox="0 0 16 30"><path d="M2 2l11 13L2 28" fill="none" stroke="#999" stroke-width="3"/></svg>

<article class="news-card" style="left:157px">
  <div class="photo" role="img" aria-label="Measuring tape around a waist" style="background:linear-gradient(160deg,#cfa999,#e8cbbb 50%,#a98a7c)"></div>
  <h5>There are many variations passages of Lorem</h5>
  <p>But I must explain to you how all this mistaken idea of denouncing pleasure and praising pain was born</p>
  <div class="btn">READ MORE</div>
</article>
<article class="news-card" style="left:463px">
  <div class="photo" role="img" aria-label="Torso with measuring tape in jeans" style="background:linear-gradient(180deg,#9fb3c9,#e0c3b2 50%,#7f97b5)"></div>
  <h5>At vero eos et accusamus et iusto odio dignissimos</h5>
  <p>These cases are perfectly simple and easy to distinguish in a free hour, when our power of choice is .</p>
  <div class="btn">READ MORE</div>
</article>
<article class="news-card" style="left:765px">
  <div class="photo" role="img" aria-label="Waist in checked shirt pinching belly fat" style="background:linear-gradient(180deg,#8a4a57,#d9b3a1 50%,#3e4f6e)"></div>
  <h5>On the other hand, we denounce with righteous</h5>
  <p>he rejects pleasures to secure other greater pleasures, or else he endures pains to avoid.</p>
  <div class="btn">READ MORE</div>
</article>

<footer class="site-footer">
  <div class="logo">LIRAVA</div>
  <div class="foot-h" style="left:435px">CONTACT US</div>
  <svg class="abs" style="left:439px;top:115px" width="9" height="12" viewBox="0 0 9 12"><path d="M4.5 0A4.5 4.5 0 0 0 0 4.5C0 8 4.5 12 4.5 12S9 8 9 4.5A4.5 4.5 0 0 0 4.5 0z" fill="#666"/><circle cx="4.5" cy="4.5" r="1.6" fill="#ebebeb"/></svg>
  <div class="foot-row" style="left:472px;top:109px">17 Lindegade,<br>Aarhus 8000</div>
  <svg class="abs" style="left:438px;top:175px" width="11" height="11" viewBox="0 0 24 24"><path fill="#666" d="M6.6 10.8a15.2 15.2 0 0 0 6.6 6.6l2.2-2.2c.3-.3.7-.4 1-.2 1.1.4 2.3.6 3.6.6.6 0 1 .4 1 1V20c0 .6-.4 1-1 1A17 17 0 0 1 3 4c0-.6.4-1 1-1h3.5c.6 0 1 .4 1 1 0 1.3.2 2.5.6 3.6.1.3 0 .7-.2 1z"/></svg>
  <div class="foot-row" style="left:472px;top:170px">555.201.4470</div>
  <svg class="abs" style="left:438px;top:219px" width="12" height="9" viewBox="0 0 12 9"><rect x=".5" y=".5" width="11" height="8" fill="none" stroke="#666"/><path d="M.5.5L6 5l5.5-4.5" fill="none" stroke="#666"/></svg>
  <div class="foot-row" style="left:472px;top:213px">info@lirava.com</div>
  <div class="foot-h" style="left:677px">MENU</div>
  <div class="foot-menu">Lirava<br>Behandlinger<br>Produkter<br>Priser<br>Kontakt</div>
  <div class="foot-h" style="left:832px">NEWSLETTER SIGNUP!</div>
  <div class="email-box"><svg width="12" height="9" viewBox="0 0 12 9"><rect x=".5" y=".5" width="11" height="8" fill="none" stroke="#666"/><path d="M.5.5L6 5l5.5-4.5" fill="none" stroke="#666"/></svg>E mail id</div>
  <div class="btn signup">SIGNUP!</div>
  <div class="foot-rule"></div>
  <div class="follow">FOLLOW US</div>
  <span class="social" style="left:212px"></span>
  <span class="social" style="left:240px"></span>
  <span class="social" style="left:268px"></span>
  <span class="social" style="left:296px"></span>
  <div class="copy">Copyrights @ 2017 All Rights Reserved</div>
</footer>

</body>
</html>
```